CalmPeak Nurses' Manifesto

Design a manifesto to inspire and motivate nurses to work at minimum standards of excellence in their nursing practice.

The manifesto will become a feature of our website, at conferences, workshops and retreats. It will also be featured on other marketing tools.

Primary Market:
Nurses and/or other healthcare professionals (specifically Doctors, Occupational Therapists, Psychologists and Social Workers).

However the manifesto is equally applicable to all nurses and healthcare professionals from new graduates to very experienced senior clinicians, administration officers,managers and healthcare executive personnel.

Mainly females and primarily 35 to 65 years old, which suggests people in this target age group have extensive experience, but have become jaded'.

The purpose of our business is to assist healthcare professionals, primarily nurses, to maintain their enthusiasm and excellence in service provision, for their benefit as well as the benefit of the clients.

I have attached:
File 1: Copy Samples and examples: which has the copy for the manifesto, examples that appeal to us and our 3 attempts.
File 2: Our colour Spec Sheet, HOWEVER the colours are not necessary limited to these colours. These colours are not in the logo that will be on the manifesto. The colours on the logo attached can/or also be used.
File 3: Prototype logo. The final logo will be available within 3 to 4 days.

Industry/Entity Type

Healthcare

Requirements
Must have
• Must use the copy as per the attached file.

It should be contemporary, eye catching and motivational.

Should not have
• MUST BE EASY TO READ. Each line MUST be clearly defined from each other.

```html
<!DOCTYPE html>
<html lang="en">
<head>
<meta charset="utf-8">
<title>CalmPeak Nurses' Manifesto</title>
<link rel="stylesheet" href="https://fonts.googleapis.com/css2?family=Source+Sans+3:wght@400;600&display=swap">
<style>
:root{
  --sky:#4fb7e8;
  --navy-blue:#1d5fa8;
  --deep-blue:#1b3e98;
  --bright-blue:#2473d9;
  --choose-blue:#3e8ee0;
  --delight-blue:#1e75b9;
  --lead-blue:#4a9fe0;
  --pale-blue:#a6d9f5;
  --band-blue:#4a8fe0;
  --magenta:#e0198c;
  --aqua:#5fd9c0;
  --green:#3a9b1f;
  --lime:#8cd025;
  --unique-green:#7cc520;
  --red:#e8211c;
  --orange:#f0701e;
  --purple:#8b5ee8;
  --brown:#8b4d14;
  --ink:#111;
  --paper:#fff;
  --logo-green:#2a7a2a;
}
*{margin:0;padding:0;box-sizing:border-box}
html,body{width:900px;height:1200px;overflow:hidden;background:var(--paper)}
.manifesto{position:relative;width:900px;height:1200px;font-family:"Source Sans 3",sans-serif;overflow:hidden}
.line{position:absolute;white-space:nowrap;line-height:1;z-index:2}
.just{text-align:justify;text-align-last:justify;white-space:normal}
.top-band{position:absolute;left:37px;top:0;width:845px;height:14px;background:var(--band-blue)}
.corner-band{position:absolute;left:20px;top:1150px;width:20px;height:50px;background:var(--pale-blue)}
.photo{position:absolute;z-index:1;left:660px;top:836px;width:222px;height:314px;background:linear-gradient(180deg,#eef8f7 0%,#a8e0dc 45%,#7fcfcb 100%)}
.dream-band{position:absolute;z-index:3;left:490px;top:1150px;width:392px;height:50px;background:var(--band-blue);color:var(--paper);font-size:30px;padding:10px 0 0 30px;line-height:1}
.dream-band b{font-weight:400;font-size:42px;opacity:.9}
.brand{position:absolute;left:60px;top:1158px;display:flex;align-items:center;gap:10px;color:var(--logo-green);font-size:26px}
.brand-mark{width:34px;height:34px;background:var(--lime)}
.vertical{transform:rotate(-90deg);transform-origin:left top}
</style>
</head>
<body>
<main class="manifesto">
  <div class="top-band"></div>

  <!-- header row -->
  <div class="line" style="left:37px;top:16px;font-size:76px;color:var(--sky)">Nurse</div>
  <div class="line" style="left:245px;top:40px;font-size:28px;color:var(--navy-blue)">Deliver</div>
  <div class="line" style="left:352px;top:16px;font-size:62px;color:var(--navy-blue)">care</div>
  <div class="line" style="left:487px;top:38px;font-size:31px;color:var(--navy-blue)">skillfully.</div>
  <div class="line" style="left:37px;top:92px;font-size:44px;color:var(--sky)">with open</div>
  <div class="line" style="left:243px;top:78px;font-size:64px;color:var(--magenta)">Learn</div>
  <div class="line" style="left:408px;top:80px;font-size:27px;letter-spacing:5px;color:var(--magenta)">something</div>
  <div class="line" style="left:408px;top:106px;font-size:29px;color:var(--magenta)">new each day.</div>
  <div class="line" style="left:37px;top:132px;font-size:43px;color:var(--aqua)">hands, hearts and minds.</div>

  <div class="line" style="left:630px;top:18px;font-size:110px;color:var(--green)">Trust</div>
  <div class="line just" style="left:630px;top:112px;width:235px;font-size:23px;color:var(--green)">your knowledge and</div>
  <div class="line just" style="left:630px;top:134px;width:235px;font-size:23px;color:var(--green)">seek advice only from</div>
  <div class="line" style="left:630px;top:150px;font-size:23px;color:var(--green)">respected <span style="font-size:32px">sources</span>.</div>

  <!-- column one -->
  <div class="line" style="left:37px;top:184px;font-size:32px;color:var(--ink)">Look after</div>
  <div class="line" style="left:197px;top:162px;font-size:56px;color:var(--ink)">yourself</div>
  <div class="line" style="left:37px;top:218px;font-size:32px;color:var(--ink)">and value your <span style="font-size:46px">health</span></div>
  <div class="line just" style="left:37px;top:260px;width:348px;font-size:29px;color:var(--ink)">as much as you value</div>
  <div class="line just" style="left:37px;top:294px;width:348px;font-size:29px;color:var(--ink)">the health of others.</div>
  <div class="line" style="left:37px;top:328px;font-size:46px;color:var(--magenta)">Be</div>
  <div class="line just" style="left:110px;top:340px;width:275px;font-size:29px;color:var(--magenta)">a lifelong learner.</div>
  <div class="line" style="left:37px;top:370px;font-size:62px;color:var(--ink)">Respect</div>
  <div class="line" style="left:256px;top:398px;font-size:24px;color:var(--ink)">the limits of</div>
  <div class="line" style="left:37px;top:428px;font-size:26px;color:var(--ink)"><span style="font-size:32px">people</span>'s knowledge and share</div>
  <div class="line just" style="left:37px;top:462px;width:348px;font-size:24px;color:var(--ink)">your knowledge generously.</div>
  <div class="line" style="left:37px;top:490px;font-size:64px;color:var(--deep-blue)">Smile</div>
  <div class="line just" style="left:244px;top:518px;width:141px;font-size:33px;color:var(--deep-blue)">and infect</div>
  <div class="line just" style="left:37px;top:550px;width:348px;font-size:32px;color:var(--deep-blue)">others with your</div>
  <div class="line just" style="left:37px;top:584px;width:348px;font-size:28px;color:var(--deep-blue)">h a p p i n e s s</div>
  <div class="line" style="left:37px;top:616px;font-size:62px;color:var(--lime)"><b style="font-weight:600">Seek</b> success</div>
  <div class="line" style="left:37px;top:670px;font-size:44px;color:var(--lime)">firstly from within.</div>
  <div class="line vertical" style="left:37px;top:832px;font-size:40px;color:var(--pale-blue)">Adopt</div>
  <div class="line" style="left:88px;top:726px;font-size:36px;color:var(--pale-blue)">a ‘can do’ attitude</div>
  <div class="line just" style="left:88px;top:761px;width:290px;font-size:33px;color:var(--pale-blue)">to everything that</div>
  <div class="line just" style="left:88px;top:796px;width:290px;font-size:33px;color:var(--pale-blue)">comes your way.</div>

  <!-- column two -->
  <div class="line" style="left:400px;top:178px;font-size:68px;color:var(--bright-blue)">Respond</div>
  <div class="line" style="left:402px;top:254px;font-size:27px;color:var(--bright-blue)">to complex situations</div>
  <div class="line" style="left:402px;top:278px;font-size:45px;color:var(--bright-blue)">innovatively,</div>
  <div class="line" style="left:402px;top:318px;font-size:45px;color:var(--bright-blue)">creatively</div>
  <div class="line" style="left:626px;top:334px;font-size:24px;color:var(--bright-blue)">and</div>
  <div class="line" style="left:402px;top:364px;font-size:42px;color:var(--bright-blue)">safely</div>
  <div class="line just" style="left:530px;top:376px;width:138px;font-size:27px;color:var(--bright-blue)">within the</div>
  <div class="line just" style="left:402px;top:406px;width:266px;font-size:27px;color:var(--bright-blue)">scope of your</div>
  <div class="line just" style="left:402px;top:438px;width:266px;font-size:26px;color:var(--bright-blue)">p r a c t i c e .</div>
  <div class="line" style="left:400px;top:472px;font-size:66px;letter-spacing:3px;color:var(--red)">Support</div>
  <div class="line" style="left:400px;top:542px;font-size:36px;color:var(--red)">your colleagues</div>
  <div class="line just" style="left:400px;top:580px;width:268px;font-size:37px;color:var(--red)">and champion</div>
  <div class="line just" style="left:400px;top:617px;width:268px;font-size:37px;color:var(--red)">their purpose.</div>
  <div class="line vertical" style="left:402px;top:832px;font-size:48px;color:var(--purple)">Always</div>
  <div class="line just" style="left:468px;top:676px;width:200px;font-size:33px;color:var(--purple)">be solution</div>
  <div class="line just" style="left:468px;top:710px;width:200px;font-size:30px;color:var(--purple)">f o c u s e d .</div>
  <div class="line just" style="left:468px;top:756px;width:392px;font-size:33px;color:var(--purple)">do the right thing</div>
  <div class="line just" style="left:468px;top:796px;width:392px;font-size:33px;color:var(--purple)">without exception.</div>

  <!-- column three -->
  <div class="line" style="left:680px;top:182px;font-size:52px;letter-spacing:1px;color:var(--choose-blue)">Choose</div>
  <div class="line just" style="left:680px;top:230px;width:182px;font-size:25px;color:var(--choose-blue)">t h o u g h t s</div>
  <div class="line just" style="left:680px;top:256px;width:182px;font-size:26px;color:var(--choose-blue)">wisely, they</div>
  <div class="line just" style="left:680px;top:284px;width:182px;font-size:26px;color:var(--choose-blue)">create your</div>
  <div class="line" style="left:680px;top:310px;font-size:44px;letter-spacing:4px;color:var(--choose-blue)">reality<span style="font-size:25px">.</span></div>
  <div class="line" style="left:680px;top:364px;font-size:36px;color:var(--orange)">Celebrate,</div>
  <div class="line just" style="left:680px;top:400px;width:182px;font-size:36px;color:var(--orange)">respect <span style="font-size:25px">and</span></div>
  <div class="line just" style="left:680px;top:437px;width:182px;font-size:36px;color:var(--orange)">v a l u e</div>
  <div class="line just" style="left:680px;top:476px;width:182px;font-size:27px;color:var(--orange)">the diversity</div>
  <div class="line just" style="left:680px;top:502px;width:182px;font-size:27px;color:var(--orange)">of Australian</div>
  <div class="line just" style="left:680px;top:532px;width:182px;font-size:24px;color:var(--orange)">c u l t u r e .</div>
  <div class="line" style="left:683px;top:562px;font-size:60px;letter-spacing:-2px;color:var(--unique-green)">You</div>
  <div class="line" style="left:820px;top:590px;font-size:26px;color:var(--unique-green)">are</div>
  <div class="line" style="left:683px;top:614px;font-size:58px;letter-spacing:-2px;color:var(--unique-green)">unique,</div>
  <div class="line just" style="left:683px;top:680px;width:178px;font-size:29px;color:var(--unique-green)">revel <span style="font-size:22px">in</span> your</div>
  <div class="line" style="left:683px;top:712px;font-size:33px;color:var(--unique-green)">individuality.</div>

  <!-- closing lines -->
  <div class="photo" role="img" aria-label="Photo of a smiling nurse in light blue scrubs holding a clipboard"></div>
  <div class="line" style="left:37px;top:836px;font-size:56px;color:var(--delight-blue)">Delight</div>
  <div class="line" style="left:218px;top:852px;font-size:37px;color:var(--delight-blue)">your clients and colleagues</div>
  <div class="line" style="left:37px;top:890px;font-size:34px;color:var(--delight-blue)">by exceeding their expectations.</div>
  <div class="line" style="left:37px;top:924px;font-size:33px;color:var(--red)">Only <span style="font-size:46px">follow</span> exceptional <span style="font-size:44px">leaders</span>.</div>
  <div class="line" style="left:37px;top:966px;font-size:60px;color:var(--brown)">Always</div>
  <div class="line" style="left:232px;top:982px;font-size:40px;color:var(--lead-blue)">If there is no one left</div>
  <div class="line" style="left:37px;top:1026px;font-size:46px;color:var(--brown)">lead with</div>
  <div class="line" style="left:232px;top:1028px;font-size:38px;color:var(--lead-blue)">to follow, then</div>
  <div class="line" style="left:493px;top:1014px;font-size:60px;color:var(--lead-blue)">lead<span style="font-size:30px">!</span></div>
  <div class="line" style="left:37px;top:1068px;font-size:44px;color:var(--brown)">purpose, passion</div>
  <div class="line" style="left:296px;top:1102px;font-size:36px;color:var(--brown)">and <span style="font-size:44px">commitment</span>.</div>

  <div class="corner-band"></div>
  <div class="brand"><span class="brand-mark"></span>CalmPeak</div>
  <div class="dream-band">Live your <b>dream</b></div>
</main>
</body>
</html>
```